Business cards for a fun web development agency

Hi,I am building a web development agency. You can read about it on the website http://kite-loft.examplehost.com. Basically, I want to focus on free and open source products and stay as far away from the corporate business feeling as possible. I want to build a community so I want the business card to feel fun and approachable (at the risk of professional if need be). I am uploading some of my image assets in various file formats. Feel free to use them or make your own if you want just keeping in theme with the website.
Industry/Entity Type
Building
Contact Information for Business Card
Company Name: Boat ShedWebsite: www.kiteloftdev.example (it's currently in alpha on http://kite-loft.examplehost.com if you want to see the them we are trying to capture)My name is: Banner B. SchaferMy email: banner@boatsheddev.comMy phone: 0431 587 904
Look and feel

```html
<!DOCTYPE html>
<html lang="en">
<head>
<meta charset="utf-8">
<title>Kite Loft – Business Cards</title>
<link href="https://fonts.googleapis.com/css2?family=Michroma&display=swap" rel="stylesheet">
<style>
  :root {
    --page: #ecebe8;
    --card-white: #f7f7f7;
    --card-shade: #e6e6e6;
    --brand-blue: #1283b6;
    --silver-light: #f2f2f2;
    --silver-dark: #9a9a9a;
    --ink-white: #ffffff;
    --ink-grey: #3f3f3f;
  }
  * { box-sizing: border-box; margin: 0; padding: 0; }
  html, body { width: 1200px; height: 828px; overflow: hidden; }
  body {
    background: var(--page);
    font-family: "Michroma", sans-serif;
    position: relative;
  }
  .card {
    position: absolute;
    width: 540px;
    height: 310px;
    background: linear-gradient(160deg, var(--card-white), var(--card-shade));
    box-shadow: 0 6px 18px rgba(0,0,0,.18);
    overflow: hidden;
  }
  .card--front { left: 50px; top: 120px; }
  .card--back { left: 610px; top: 400px; }
  .card__wave { position: absolute; inset: 0; width: 100%; height: 100%; }

  .brand {
    position: absolute;
    display: flex;
    align-items: center;
    gap: 8px;
    color: var(--brand-blue);
    font-size: 26px;
    letter-spacing: 1px;
    white-space: nowrap;
  }
  .brand__dot {
    width: 22px; height: 22px;
    border-radius: 50%;
    background: var(--brand-blue);
  }
  .card--front .brand { left: 210px; top: 48px; }
  .card--back .brand { left: 36px; top: 88px; font-size: 23px; }
  .card--back .brand__dot { width: 20px; height: 20px; }

  .holder {
    position: absolute;
    right: 30px; top: 26px;
    text-align: right;
    color: var(--brand-blue);
  }
  .holder__name { font-size: 15px; letter-spacing: .5px; }
  .holder__title { font-size: 8px; color: var(--ink-grey); margin-top: 4px; letter-spacing: .5px; }

  .address {
    position: absolute;
    right: 30px; top: 138px;
    text-align: right;
    color: var(--ink-white);
    font-size: 11px;
    line-height: 1.6;
  }
  .contacts {
    position: absolute;
    left: 26px; bottom: 14px;
    list-style: none;
    color: var(--ink-white);
    font-size: 9px;
    line-height: 1;
  }
  .contacts li { display: flex; align-items: center; gap: 10px; height: 14px; }
  .contacts svg { width: 10px; height: 10px; fill: var(--ink-white); flex: none; }
</style>
</head>
<body>

<section class="card card--front" aria-label="Card front">
  <svg class="card__wave" viewBox="0 0 540 310" preserveAspectRatio="none" aria-hidden="true">
    <defs>
      <linearGradient id="silverFront" x1="0" y1="0" x2="1" y2="0">
        <stop offset="0" stop-color="var(--silver-light)"/>
        <stop offset=".45" stop-color="var(--silver-dark)"/>
        <stop offset=".6" stop-color="var(--silver-light)"/>
        <stop offset="1" stop-color="var(--silver-dark)"/>
      </linearGradient>
    </defs>
    <path d="M0,310 L0,218 C110,205 200,170 290,120 C370,78 450,62 540,58 L540,310 Z" fill="url(#silverFront)"/>
    <path d="M0,310 L0,236 C110,224 210,188 300,140 C380,98 455,82 540,80 L540,310 Z" fill="var(--brand-blue)"/>
  </svg>
  <div class="brand"><span>KITE LOFT</span><span class="brand__dot"></span></div>
</section>

<section class="card card--back" aria-label="Card back">
  <svg class="card__wave" viewBox="0 0 540 310" preserveAspectRatio="none" aria-hidden="true">
    <defs>
      <linearGradient id="silverBack" x1="0" y1="0" x2="1" y2="0">
        <stop offset="0" stop-color="var(--silver-light)"/>
        <stop offset=".45" stop-color="var(--silver-dark)"/>
        <stop offset=".6" stop-color="var(--silver-light)"/>
        <stop offset="1" stop-color="var(--silver-dark)"/>
      </linearGradient>
    </defs>
    <path d="M0,310 L0,192 C120,182 220,148 310,112 C390,82 460,74 540,72 L540,310 Z" fill="url(#silverBack)"/>
    <path d="M0,310 L0,210 C120,200 220,166 310,130 C390,100 460,92 540,90 L540,310 Z" fill="var(--brand-blue)"/>
  </svg>

  <div class="brand"><span>KITE LOFT</span><span class="brand__dot"></span></div>

  <div class="holder">
    <p class="holder__name">CORWIN T. ALDOUS</p>
    <p class="holder__title">MANAGING DIRECTOR</p>
  </div>

  <p class="address">027,4th floor,Quay<br>Harbour Lane QLD</p>

  <ul class="contacts">
    <li><svg viewBox="0 0 12 12"><path d="M2 1h3l1 3-1.5 1a6 6 0 0 0 2.5 2.5L8 6l3 1v3c0 .6-.4 1-1 1A9 9 0 0 1 1 2c0-.6.4-1 1-1z"/></svg>0431 587 904</li>
    <li><svg viewBox="0 0 12 12"><path d="M3 0h6v12H3zM4 1.5v8h4v-8z"/></svg>0431 587 905</li>
    <li><svg viewBox="0 0 12 12"><path d="M1 4h3V0h6v12H1zM5 1v3h4V1zM2 6v1h2V6zm4 0v1h2V6zM2 9v1h2V9zm4 0v1h2V9z"/></svg>0431 587 906</li>
    <li><svg viewBox="0 0 12 12"><path d="M0 2h12v8H0zM1 3l5 4 5-4z"/></svg>corwin@kiteloftdev.example</li>
    <li><svg viewBox="0 0 12 12"><path d="M6 0a6 6 0 1 0 0 12A6 6 0 0 0 6 0zm0 1c1 1 1.5 3 1.5 5S7 10 6 11C5 10 4.5 8 4.5 6S5 2 6 1zM1.2 5.5h9.6v1H1.2z"/></svg>www.kiteloftdev.example</li>
  </ul>
</section>

</body>
</html>
```